Design a compelling Tarnwove Business Card that will drive people to my site

I want a business card that I can give to people—less to tell them who I am and more to direct them to my website. My website is a portal for Pelmor Aquatics Officials and a place for people who want to become Pelmor Aquatics Officials.
I am uploading my official company logo as well as a business card mockup that I did on my own. Please feel free to completely stray from this design.
I've included a screen recording of the homepage of my website as well.
Target Market(s)
Pelmor Aquatics Officials and people who desire to become one
Contact Information for Business Card
website url
Look and feel
Each slider illustrates characteristics of the customer's brand and the style your logo design should communicate.

```html
<!DOCTYPE html>
<html lang="en">
<head>
<meta charset="utf-8">
<title>Tarnwove Business Card</title>
<link rel="stylesheet" href="https://fonts.googleapis.com/css2?family=Poppins:wght@400;500;600&family=Inter:wght@600&display=swap">
<style>
  :root {
    --navy: #2e4e95;
    --brand: #3a55a4;
    --pale: #c5cfe8;
    --soft: #93a8d8;
    --white: #ffffff;
    --stage: #f0f0f0;
  }
  * { margin: 0; padding: 0; box-sizing: border-box; }
  html, body { width: 1200px; height: 987px; overflow: hidden; }
  body { background: var(--stage); position: relative; font-family: "Poppins", sans-serif; }

  .card { position: absolute; left: 245px; width: 710px; height: 405px; overflow: hidden; }

  /* Front */
  .card-front { top: 68px; background: var(--navy); }
  .front-name {
    position: absolute; left: 0; right: 0; top: 155px;
    text-align: center; color: var(--white);
    font-weight: 600; font-size: 80px; line-height: 1; letter-spacing: -1px;
  }
  .front-rule {
    position: absolute; left: 290px; top: 292px; width: 130px; height: 4px; border-radius: 2px;
    background: linear-gradient(90deg, var(--pale), rgba(197,207,232,0.6) 60%, rgba(58,85,164,0.4));
  }
  .tagline {
    position: absolute; left: 0; right: 0; top: 351px;
    text-align: center; font-family: "Inter", sans-serif; font-weight: 600;
    font-size: 29px; line-height: 1; letter-spacing: 0.3px; color: var(--white);
  }
  .tagline .tagline-lead { color: var(--pale); }

  /* Back */
  .card-back { top: 514px; background: var(--white); }
  .edge-bar { position: absolute; top: 101px; width: 16px; height: 203px; background: var(--brand); }
  .edge-bar.left { left: 0; }
  .edge-bar.right { right: 0; }
  .back-divider { position: absolute; left: 354px; top: 81px; width: 1px; height: 244px; background: var(--brand); }
  .back-name {
    position: absolute; left: 26px; top: 190px; width: 300px;
    color: var(--brand); font-weight: 500; font-size: 60px; line-height: 1; letter-spacing: -1.5px;
  }
  .person { position: absolute; left: 408px; top: 112px; }
  .person-name { color: var(--brand); font-weight: 600; font-size: 31px; line-height: 1.1; }
  .person-role { color: var(--soft); font-weight: 400; font-size: 18px; line-height: 1; margin-top: 6px; }
  .contacts { position: absolute; left: 407px; top: 210px; list-style: none; }
  .contacts li { display: flex; align-items: center; height: 25.5px; color: var(--soft); font-size: 19px; letter-spacing: 0.3px; }
  .contacts svg { width: 17px; height: 17px; margin-right: 11px; flex: none; }
</style>
</head>
<body>
  <section class="card card-front" aria-label="Card front">
    <div class="front-name">tarnwove.com</div>
    <div class="front-rule"></div>
    <p class="tagline"><span class="tagline-lead">The Poolside</span> Referee's Gateway</p>
  </section>

  <section class="card card-back" aria-label="Card back">
    <div class="edge-bar left"></div>
    <div class="edge-bar right"></div>
    <div class="back-name">tarnwove</div>
    <div class="back-divider"></div>
    <div class="person">
      <h1 class="person-name">Daniel Marrow</h1>
      <p class="person-role">CEO &amp; Founder</p>
    </div>
    <ul class="contacts">
      <li>
        <svg viewBox="0 0 24 24" aria-hidden="true"><path fill="#3a55a4" d="M6.6 10.8c1.4 2.8 3.8 5.1 6.6 6.6l2.2-2.2c.3-.3.7-.4 1-.2 1.1.4 2.3.6 3.6.6.6 0 1 .4 1 1V20c0 .6-.4 1-1 1C10.6 21 3 13.4 3 4c0-.6.4-1 1-1h3.5c.6 0 1 .4 1 1 0 1.3.2 2.5.6 3.6.1.3 0 .7-.2 1z"/><path fill="none" stroke="#3a55a4" stroke-width="1.6" stroke-linecap="round" d="M14 3.5a7 7 0 0 1 6.5 6.5M14 7a3.5 3.5 0 0 1 3 3"/></svg>
        (555) 014-2273
      </li>
      <li>
        <svg viewBox="0 0 24 24" aria-hidden="true"><circle cx="12" cy="12" r="10" fill="#3a55a4"/><path fill="none" stroke="#fff" stroke-width="1.3" d="M2 12h20M12 2c3 3 3 17 0 20M12 2c-3 3-3 17 0 20"/></svg>
        www.tarnwove.com
      </li>
      <li>
        <svg viewBox="0 0 24 24" aria-hidden="true"><path fill="#3a55a4" d="M2 9l10-7 10 7v12H2z"/><rect x="6" y="6" width="12" height="9" fill="#fff"/><path fill="none" stroke="#3a55a4" stroke-width="1.2" d="M2 9l10 7 10-7M2 21l7-6M22 21l-7-6"/><circle cx="12" cy="10" r="2" fill="none" stroke="#3a55a4" stroke-width="1.2"/></svg>
        dan@tarnwove.com
      </li>
    </ul>
  </section>
</body>
</html>
```